Marlow Sail Works President Business Card Carbon fiber catamarans

Hi.. I need a new business card design.. I am the President of a high tech yacht builder. We build Carbon Fiber go fast catamarans... Maybe we use the file I am sharing to you as the back of the card.. We need to look cool and crisp ...

Target Market(s)

Affluent People who will purchase a cool yacht

Industry/Entity Type

Custom Yacht Builder

Contact Information for Business Card

Dean Pellway , President, 731.508.2164 USA

Font styles to use
Serif

Requirements
Must have
• the clean crisp cool feel
Nice to have
• clean and crisp
Should not have
• Bold ugly

```html
<!DOCTYPE html>
<html lang="en">
<head>
<meta charset="utf-8">
<title>Marlow Sail Works – Business Card</title>
<link href="https://fonts.googleapis.com/css2?family=Michroma&display=swap" rel="stylesheet">
<style>
  :root {
    --backdrop: #0a0a0a;
    --card-top: #2d2d2f;
    --card-bottom: #222224;
    --silver: #d4d4d6;
    --silver-dim: #a9a9ad;
    --rule: #8a8a8e;
    --mark: #3a3a3d;
  }
  * { margin: 0; padding: 0; box-sizing: border-box; }
  html, body {
    width: 1200px; height: 820px; overflow: hidden;
    background: var(--backdrop);
    font-family: "Michroma", sans-serif;
    color: var(--silver);
  }
  .canvas { position: relative; width: 1200px; height: 820px; }

  .card {
    position: absolute;
    width: 525px; height: 300px;
    background: linear-gradient(160deg, var(--card-top), var(--card-bottom));
    border-radius: 3px;
    box-shadow: 0 18px 40px rgba(0,0,0,.7);
  }
  .card--front { left: 45px; top: 400px; }
  .card--back  { left: 630px; top: 120px; }

  /* front */
  .brand {
    position: absolute; left: 200px; top: 34px;
    display: flex; align-items: center; gap: 14px;
  }
  .brand__dot {
    width: 38px; height: 38px; border-radius: 50%;
    background: var(--silver-dim);
  }
  .brand__name {
    font-size: 19px; line-height: 1.15; letter-spacing: 3px;
    text-transform: uppercase; color: var(--silver);
  }
  .brand__name span { display: block; font-size: 19px; }
  .rule-top {
    position: absolute; left: 200px; right: 28px; top: 108px;
    height: 1px; background: var(--rule);
  }
  .person { position: absolute; left: 32px; top: 138px; }
  .person__name {
    font-size: 15px; letter-spacing: 3px; text-transform: uppercase;
  }
  .person__role {
    margin-top: 6px; font-size: 10px; letter-spacing: 2px;
    font-variant: small-caps; color: var(--silver-dim);
  }
  .rule-person {
    position: absolute; left: 32px; top: 186px; width: 200px;
    height: 1px; background: var(--rule);
  }
  .contact {
    position: absolute; left: 32px; top: 198px;
    list-style: none;
  }
  .contact__row {
    display: flex; align-items: center; gap: 10px;
    height: 22px; font-size: 10px; letter-spacing: 2px;
    text-transform: lowercase;
  }
  .contact__row--address { text-transform: none; font-variant: small-caps; margin-top: 2px; }
  .contact__icon { width: 13px; height: 13px; flex: none; }

  /* back */
  .back-circle {
    position: absolute; left: 70px; top: 70px;
    width: 160px; height: 160px; border-radius: 50%;
    background: var(--mark);
  }
  .back-name {
    position: absolute; left: 262px; top: 118px;
    font-size: 24px; line-height: 1.2; letter-spacing: 4px;
    text-transform: uppercase; color: var(--silver);
  }
  .back-name span { display: block; font-size: 24px; }
</style>
</head>
<body>
<main class="canvas">

  <section class="card card--front" aria-label="Business card front">
    <div class="brand">
      <div class="brand__dot"></div>
      <div class="brand__name">Marlow<span>Sail Works</span></div>
    </div>
    <div class="rule-top"></div>

    <div class="person">
      <p class="person__name">Dean Pellway</p>
      <p class="person__role">President</p>
    </div>
    <div class="rule-person"></div>

    <ul class="contact">
      <li class="contact__row">
        <svg class="contact__icon" viewBox="0 0 16 16" fill="none" stroke="currentColor" stroke-width="1.4">
          <path d="M4 1.5l2.2 3-1.4 1.6a8 8 0 0 0 5.1 5.1l1.6-1.4 3 2.2-1.3 2.3C7.5 14.5 1.5 8.5 1.7 2.8z"/>
        </svg>
        731.508.2164
      </li>
      <li class="contact__row">
        <svg class="contact__icon" viewBox="0 0 16 16" fill="none" stroke="currentColor" stroke-width="1.4">
          <rect x="1.5" y="3.5" width="13" height="9"/><path d="M1.5 3.5l6.5 5 6.5-5"/>
        </svg>
        info@marlowsail.com
      </li>
      <li class="contact__row">
        <svg class="contact__icon" viewBox="0 0 16 16" fill="none" stroke="currentColor" stroke-width="1.2">
          <circle cx="8" cy="8" r="6.5"/><ellipse cx="8" cy="8" rx="3" ry="6.5"/><path d="M1.5 8h13M2.5 4.8h11M2.5 11.2h11"/>
        </svg>
        www.marlowsailworks.com
      </li>
      <li class="contact__row contact__row--address">
        <svg class="contact__icon" viewBox="0 0 16 16" fill="currentColor">
          <path d="M8 1a5 5 0 0 0-5 5c0 3.8 5 9 5 9s5-5.2 5-9a5 5 0 0 0-5-5zm0 7a2 2 0 1 1 0-4 2 2 0 0 1 0 4z"/>
        </svg>
        Rhode Island 02871, USA
      </li>
    </ul>
  </section>

  <section class="card card--back" aria-label="Business card back">
    <div class="back-circle"></div>
    <div class="back-name">Marlow<span>Sail Works</span></div>
  </section>

</main>
</body>
</html>
```